Insurance Agency website design for Brellow Cover Insurance, LP

Build a website for Brellow Cover Insurance, LP which sells Homeowners, Auto, Renters, Condo, Flood, Disability, Life, Umbrella, and health insurance. We need the coolest insurance agency website out there to get quotes, contact us, or get additional information. Please list the following insurance companies we work with: Varnix, Ostle, Meridale Mutual, Quillor, Dunmarrow, KGZ, and Pellwick.

Make a design similar to https://www.fernagentry.com/

Selling personal insurance policies

```html
<!DOCTYPE html>
<html lang="en">
<head>
<meta charset="utf-8">
<title>Brellow Cover Insurance, LP</title>
<link rel="stylesheet" href="https://fonts.googleapis.com/css2?family=Poppins:wght@400;500;600;700;800&family=Open+Sans:wght@400;600;700&display=swap">
<style>
:root{
  --navy:#0b2f66;
  --deep:#0a2452;
  --blue:#1550a8;
  --accent:#1f74d6;
  --orange:#f47a1f;
  --light:#eef2f7;
  --ink:#1d2433;
  --muted:#4a5566;
  --white:#ffffff;
}
*{box-sizing:border-box;margin:0;padding:0}
html,body{width:1200px;height:4116px;overflow:hidden}
body{font-family:"Open Sans",sans-serif;color:var(--ink);background:var(--white);position:relative}
h1,h2,h3,.btn,.nav a{font-family:"Poppins",sans-serif}
section,header,footer{position:absolute;left:0;width:1200px}
.btn{display:inline-flex;align-items:center;gap:10px;background:var(--orange);color:var(--white);font-weight:600;font-size:15px;border-radius:24px;padding:12px 30px;text-transform:uppercase;letter-spacing:.5px;white-space:nowrap}
.blue-word{color:var(--accent)}

/* header */
.site-header{top:0;height:180px;background:var(--white)}
.brand{position:absolute;left:110px;top:38px;display:flex;align-items:center;gap:14px}
.brand-mark{width:46px;height:46px;background:var(--blue);border-radius:6px}
.brand-name{font-family:"Poppins",sans-serif;font-weight:700;font-size:22px;color:var(--navy);line-height:1.1}
.contact-bar{position:absolute;right:110px;top:14px;display:flex;align-items:center;gap:34px}
.contact-item{display:flex;align-items:center;gap:10px;font-size:12px;color:var(--muted)}
.contact-item b{display:block;font-size:15px;color:var(--navy)}
.ico-circle{width:34px;height:34px;border-radius:50%;background:var(--navy);display:flex;align-items:center;justify-content:center}
.btn-outline{border:2px solid var(--orange);color:var(--navy);background:var(--white);padding:8px 26px;font-size:14px}
.nav{position:absolute;right:150px;top:112px;display:flex;gap:50px}
.nav a{font-size:14px;font-weight:500;color:var(--navy);text-decoration:none;padding-bottom:8px}
.nav a.active{color:var(--accent);border-bottom:3px solid var(--accent)}

/* hero */
.hero{top:180px;height:980px;background:linear-gradient(180deg,#3a6aa8 0%,#4f7fb8 45%,#8fa9c8 100%)}
.hero-veil{position:absolute;inset:0;background:linear-gradient(180deg,rgba(11,47,102,.55),rgba(11,47,102,.15))}
.hero-lead{position:absolute;left:170px;top:60px;width:860px;text-align:center;color:var(--white);font-family:"Poppins",sans-serif;font-weight:600;font-size:27px;line-height:1.42}
.quote-card{position:absolute;left:120px;top:530px;width:400px;height:376px;background:var(--navy);padding:30px 30px;border-bottom:6px solid var(--orange)}
.quote-card h2{color:var(--white);font-size:34px;font-weight:700;margin-bottom:22px}
.field-row{display:flex;gap:12px;margin-bottom:16px}
.field{flex:1;height:44px;background:var(--white);border-radius:3px;display:flex;align-items:center;padding:0 14px;font-size:14px;color:#6a7383}
.quote-card .btn{width:100%;justify-content:center;border-radius:3px;margin-top:4px}
.hero-frame{position:absolute;left:590px;top:300px;width:520px;height:590px}
.hero-photo{position:absolute;left:20px;top:30px;width:480px;height:530px;clip-path:polygon(0 0,60% 0,78% 8%,100% 8%,100% 100%,0 100%);background:linear-gradient(135deg,#c9b9a3,#e7ddd0 55%,#a88f74)}

/* about */
.about{top:1160px;height:420px;text-align:center}
.about h2{margin-top:40px;font-size:40px;font-weight:700;color:var(--navy)}
.about p{width:900px;margin:20px auto 0;font-size:16px;line-height:1.6;color:var(--muted)}
.about p strong{color:var(--blue);font-weight:600}
.about .partners{margin-top:12px;font-size:15px;color:var(--navy)}
.about .partners b{font-weight:700}
.about .btn{margin-top:20px}

/* protection */
.protection{top:1580px;height:880px;background:linear-gradient(160deg,var(--blue),var(--navy));text-align:center}
.protection h2{margin:60px auto 0;width:940px;color:var(--white);font-size:38px;font-weight:700;line-height:1.35}
.service-grid{position:absolute;left:120px;top:270px;width:960px;display:grid;grid-template-columns:repeat(4,240px);grid-template-rows:repeat(2,230px)}
.service{display:flex;flex-direction:column;align-items:center;justify-content:center;gap:22px;color:var(--white);font-family:"Poppins",sans-serif;font-weight:600;font-size:15px}
.service.tint{background:rgba(255,255,255,.12);border:1px solid rgba(255,255,255,.3)}
.service.link span{text-decoration:underline}
.also-offer{position:absolute;left:0;top:744px;width:1200px;color:var(--white);font-family:"Poppins",sans-serif;font-weight:600;font-size:15px;letter-spacing:.5px}
.protection .btn-white{position:absolute;left:525px;top:790px;background:var(--white);color:var(--navy)}

/* get a quote */
.cta{top:2460px;height:500px;background:var(--light)}
.cta-photo{position:absolute;left:120px;top:80px;width:340px;height:360px;clip-path:polygon(0 0,100% 0,100% 70%,50% 100%,0 70%);background:linear-gradient(135deg,#d8cdbf,#b9a48f)}
.cta-text{position:absolute;left:600px;top:120px;width:480px}
.cta-text h2{font-size:40px;font-weight:700;color:var(--navy)}
.cta-text p{margin:18px 0 26px;font-size:16px;line-height:1.6;color:var(--muted)}

/* basic info */
.basic-info{top:2960px;height:660px}
.basic-info h2{position:absolute;left:110px;top:90px;font-size:36px;font-weight:700;color:var(--navy)}
.info-form{position:absolute;left:110px;top:170px;width:480px}
.info-form p{font-size:17px;line-height:1.55;color:var(--muted);margin-bottom:28px;padding-left:50px}
.info-form label{display:block;font-size:14px;color:var(--muted);margin-bottom:8px;padding-left:10px}
.info-input{height:40px;border:1px solid #c9d0da;border-radius:3px;display:flex;align-items:center;gap:10px;padding:0 12px;font-size:13px;color:#8a93a2;margin-bottom:20px;margin-left:10px;width:470px}
.info-form .btn{margin-left:10px;margin-top:16px}
.building{position:absolute;left:720px;top:110px;width:300px;height:420px;clip-path:polygon(0 0,35% 0,50% 6%,65% 0,100% 0,100% 78%,50% 100%,0 78%);background:linear-gradient(180deg,#9cc4ea,#e6edf2 55%,#9db08a)}

/* newsletter + footer */
.newsletter{top:3620px;height:140px;background:var(--navy)}
.newsletter h3{position:absolute;left:190px;top:54px;color:var(--white);font-size:24px;font-weight:600;white-space:nowrap}
.nl-input{position:absolute;left:640px;top:46px;width:230px;height:48px;background:var(--white);border-radius:3px;display:flex;align-items:center;padding:0 14px;font-size:13px;color:#8a93a2}
.newsletter .btn{position:absolute;left:890px;top:46px;height:48px}
.site-footer{top:3760px;height:356px;background:var(--deep);color:#cfd7e6}
.foot-cols{position:absolute;left:80px;top:40px;display:flex;gap:70px}
.foot-col h3{color:var(--white);font-size:22px;font-weight:700;margin-bottom:18px}
.foot-col p,.foot-col li{font-size:14px;line-height:1.8;list-style:none}
.foot-col.about-col{width:270px}
.contact-line{display:flex;gap:10px;align-items:center}
.socials{position:absolute;left:80px;top:310px;display:flex;gap:10px}
.socials span{width:22px;height:22px;border-radius:50%;border:2px solid #cfd7e6}
.copyright{position:absolute;right:130px;top:312px;font-size:13px}
.lang{position:absolute;right:40px;top:312px;font-size:13px}
</style>
</head>
<body>

<header class="site-header">
  <div class="brand"><span class="brand-mark"></span><span class="brand-name">Brellow Cover<br>Insurance, LP</span></div>
  <div class="contact-bar">
    <div class="contact-item"><span class="ico-circle"><svg width="16" height="16" viewBox="0 0 24 24"><path d="M6.6 10.8a15 15 0 006.6 6.6l2.2-2.2a1 1 0 011-.25 11.4 11.4 0 003.6.57 1 1 0 011 1V20a1 1 0 01-1 1A17 17 0 013 4a1 1 0 011-1h3.5a1 1 0 011 1c0 1.25.2 2.45.57 3.57a1 1 0 01-.25 1z" fill="#fff"/></svg></span><div>OUR INSURANCE<b>(555) 218-3390</b></div></div>
    <div class="contact-item"><span class="ico-circle"><svg width="16" height="16" viewBox="0 0 24 24"><rect x="3" y="5" width="18" height="14" rx="2" fill="none" stroke="#fff" stroke-width="2"/><path d="M3 6l9 7 9-7" fill="none" stroke="#fff" stroke-width="2"/></svg></span><div>CHAT HERE<b>info@brellowcover.com</b></div></div>
    <span class="btn btn-outline">Get a Quote →</span>
  </div>
  <nav class="nav"><a class="active">HOME</a><a>ABOUT US</a><a>GET A QUOTE</a></nav>
</header>

<section class="hero">
  <div class="hero-veil" role="img" aria-label="Photo of a suburban family home under a blue sky"></div>
  <p class="hero-lead">At Brellow Cover Insurance, we understand that your peace of mind is invaluable. Our mission is to protect what matters most to you: your home, your vehicle, your health, and your loved ones. With our comprehensive range of insurance solutions, we are dedicated to safeguarding your assets and providing you with the security you deserve.</p>
  <div class="quote-card">
    <h2>FREE GET A QUOTE</h2>
    <div class="field-row"><div class="field">First name</div><div class="field">Last name</div></div>
    <div class="field-row"><div class="field">Phone Number</div></div>
    <div class="field-row"><div class="field">Email address</div></div>
    <span class="btn">Submit Now →</span>
  </div>
  <div class="hero-frame">
    <svg width="520" height="590" style="position:absolute;left:0;top:0"><path d="M10 20 H320 L410 60 H510 V580 H10 Z" fill="none" stroke="#fff" stroke-width="6"/></svg>
    <div class="hero-photo" role="img" aria-label="Photo of a family sitting on the floor of their living room"></div>
  </div>
</section>

<section class="about">
  <h2>ABOUT <span class="blue-word">BRELLOW COVER</span> INSURANCE</h2>
  <p>Brellow Cover Insurance is a full-service, independent insurance agency with over three decades of experience in delivering comprehensive insurance solutions to individuals. <strong>We proudly offer a diverse portfolio of products from more than 20 of the most reputable and financially secure companies in the industry. Our dedicated team of over 50 skilled professionals is committed to customizing these products and services to meet the unique needs of each client.</strong> At Brellow Cover Insurance, our experts are focused on addressing the individual needs of our clients, ensuring exceptional service and support at every step.</p>
  <p class="partners"><b>Companies we work with:</b> Varnix · Ostle · Meridale Mutual · Quillor · Dunmarrow · KGZ · Pellwick</p>
  <span class="btn">Learn More About →</span>
</section>

<section class="protection">
  <h2>NOW, MORE SPECIFICALLY, WHAT TYPE OS PERSONAL PROTECTION ARE YOU LOOKING FOR ?</h2>
  <div class="service-grid">
    <div class="service tint"><svg width="64" height="56" viewBox="0 0 64 56" fill="none" stroke="#fff" stroke-width="3"><path d="M4 28 L32 4 L60 28"/><path d="M12 22 V52 H52 V22"/><rect x="26" y="34" width="12" height="18"/></svg>HOMEOWNERS INSURANCE</div>
    <div class="service"><svg width="72" height="40" viewBox="0 0 72 40" fill="none" stroke="#fff" stroke-width="3"><path d="M4 28 V20 L16 18 L26 6 H50 L60 18 L68 20 V28 Z"/><circle cx="18" cy="30" r="6"/><circle cx="54" cy="30" r="6"/></svg>AUTO INSURANCE</div>
    <div class="service link"><svg width="64" height="56" viewBox="0 0 64 56" fill="none" stroke="#fff" stroke-width="3"><path d="M20 4 L32 14 L44 4 M24 14 H40 V26 H24 Z"/><path d="M4 40 C20 30 30 36 40 36 H52 L60 30 M4 52 H36 L60 40"/></svg><span>RENTERS INSURANCE</span></div>
    <div class="service tint"><svg width="56" height="60" viewBox="0 0 56 60" fill="none" stroke="#fff" stroke-width="3"><rect x="8" y="8" width="40" height="48"/><path d="M16 18h8M32 18h8M16 30h8M32 30h8M16 42h8M32 42h8M4 56h48"/></svg>CONDO INSURANCE</div>
    <div class="service"><svg width="64" height="60" viewBox="0 0 64 60" fill="none" stroke="#fff" stroke-width="3"><path d="M4 28 C4 10 60 10 60 28 Z"/><path d="M32 28 V50 C32 56 24 56 24 50"/></svg>UMBRELLA INSURANCE</div>
    <div class="service tint"><svg width="64" height="60" viewBox="0 0 64 60" fill="none" stroke="#fff" stroke-width="3"><path d="M32 30 C20 20 24 8 32 14 C40 8 44 20 32 30 Z"/><path d="M4 34 C14 30 20 48 30 54 M60 34 C50 30 44 48 34 54"/></svg>HEALTH INSURANCE</div>
    <div class="service"><svg width="60" height="60" viewBox="0 0 60 60" fill="none" stroke="#fff" stroke-width="3"><circle cx="26" cy="8" r="5"/><path d="M26 16 V34 H42 L48 50"/><path d="M18 26 A16 16 0 1 0 38 48"/></svg>DISABILITY INSURANCE</div>
    <div class="service tint"><svg width="64" height="60" viewBox="0 0 64 60" fill="none" stroke="#fff" stroke-width="3"><path d="M10 26 L32 8 L54 26 V40 H10 Z"/><path d="M4 48 C12 42 18 54 26 48 C34 42 40 54 48 48 C54 44 58 48 60 48"/></svg>FLOOD INSURANCE</div>
  </div>
  <p class="also-offer">ALSO AVAILABLE: LIFE INSURANCE</p>
  <span class="btn btn-white">View More →</span>
</section>

<section class="cta">
  <div class="cta-photo" role="img" aria-label="Photo of an agent shaking hands with a client across a desk"></div>
  <div class="cta-text">
    <h2>GET A <span class="blue-word">QUOTE</span></h2>
    <p>We believe that securing your home is one of the most important decisions you can make. Obtaining a comprehensive insurance quote is essential to understanding your coverage options and ensuring that your property is adequately protected against unforeseen events.</p>
    <span class="btn">Contact Us Today →</span>
  </div>
</section>

<section class="basic-info">
  <h2>SOME BASIC <span class="blue-word">INFORMATION</span></h2>
  <div class="info-form">
    <p>The address of your personal property will help in finding the right local agent for you.</p>
    <label>Enter the address of your insurable property:</label>
    <div class="info-input"><svg width="12" height="14" viewBox="0 0 12 14"><path d="M6 1a4 4 0 00-4 4c0 3 4 8 4 8s4-5 4-8a4 4 0 00-4-4z" fill="#8a93a2"/></svg>Enter street address</div>
    <label>Zip code (required):</label>
    <div class="info-input"><svg width="12" height="14" viewBox="0 0 12 14"><path d="M6 1a4 4 0 00-4 4c0 3 4 8 4 8s4-5 4-8a4 4 0 00-4-4z" fill="#8a93a2"/></svg>ZIP code</div>
    <span class="btn">Next →</span>
  </div>
  <div class="building" role="img" aria-label="Photo of a modern apartment building"></div>
</section>

<section class="newsletter">
  <h3>NEWSLETTER SUBSCRIPTION</h3>
  <div class="nl-input">Enter your E-mail</div>
  <span class="btn">Subscribe →</span>
</section>

<footer class="site-footer">
  <div class="foot-cols">
    <div class="foot-col about-col"><h3>ABOUT US</h3><p>We proudly offer a diverse portfolio of products from more than 20 of the most reputable and financially secure companies in the industry. Our dedicated team of over 50 skilled professionals.</p></div>
    <div class="foot-col"><h3>QUICK LINKS</h3><ul><li>Terms of Service</li><li>Privacy Policy</li><li>Site Map</li><li>Our Locations</li><li>Contact Us</li></ul></div>
    <div class="foot-col"><h3>ABOUT INFO</h3><ul><li>Home</li><li>About Us</li><li>Get a Quote</li></ul></div>
    <div class="foot-col"><h3>CONTACT US</h3><ul>
      <li class="contact-line"><svg width="12" height="14" viewBox="0 0 12 14"><path d="M6 1a4 4 0 00-4 4c0 3 4 8 4 8s4-5 4-8a4 4 0 00-4-4z" fill="#cfd7e6"/></svg>United States, Brellow Cover Insurance, LP</li>
      <li class="contact-line"><svg width="12" height="12" viewBox="0 0 24 24"><path d="M6.6 10.8a15 15 0 006.6 6.6l2.2-2.2a1 1 0 011-.25 11.4 11.4 0 003.6.57 1 1 0 011 1V20a1 1 0 01-1 1A17 17 0 013 4a1 1 0 011-1h3.5a1 1 0 011 1c0 1.25.2 2.45.57 3.57a1 1 0 01-.25 1z" fill="#cfd7e6"/></svg>(555) 218-3390</li>
      <li class="contact-line"><svg width="12" height="12" viewBox="0 0 24 24"><rect x="3" y="5" width="18" height="14" rx="2" fill="none" stroke="#cfd7e6" stroke-width="2"/><path d="M3 6l9 7 9-7" fill="none" stroke="#cfd7e6" stroke-width="2"/></svg>info@brellowcover.com</li>
    </ul></div>
  </div>
  <div class="socials"><span></span><span></span><span></span><span></span></div>
  <p class="copyright">Copyright © 2023 Brellow Cover Insurance, LP. All rights reserved.</p>
  <p class="lang">EN</p>
</footer>

</body>
</html>
```